Business Card Design for a Personal Trainer

I need a business card design for my job as a personal trainer. It should have a unique, modern and exclusive design. On the front there should be only my logo with my name and my job. 0162/3819204 Tobias Lendhart Wiesengrundweg 14 80417 Munich Germany The most important contact information is the web adress. it can be bigger than the rest, but its not necessary. The card should be 8,5cmx5,5cm big. Font: Roboto. Colors: black, white, gray, 56c1ff.

```html
<!DOCTYPE html>
<html lang="de">
<head>
<meta charset="utf-8">
<title>Tobias Lendhart – Personal Trainer Business Card</title>
<link rel="stylesheet" href="https://fonts.googleapis.com/css2?family=Roboto:wght@300;400;500&family=Sue+Ellen+Francisco&display=swap">
<style>
  :root {
    --bg: #d9d9d9;
    --card-white: #f4f4f4;
    --card-black: #050505;
    --ink: #1a1a1a;
    --accent-red: #8a2b2e;
    --band: #4a2424;
    --photo-dark: #5d5f60;
    --photo-light: #a3a8aa;
    --white: #ffffff;
  }
  * { box-sizing: border-box; margin: 0; padding: 0; }
  html, body { width: 1200px; height: 864px; overflow: hidden; }
  body {
    background: var(--bg);
    font-family: "Roboto", Arial, sans-serif;
    color: var(--ink);
    display: flex;
    align-items: center;
    justify-content: center;
    gap: 40px;
  }
  .card {
    position: relative;
    width: 540px;
    height: 349px;
    overflow: hidden;
    box-shadow: 0 6px 18px rgba(0,0,0,0.18);
  }
  .card--front { background: var(--card-white); }
  .card--back { background: var(--card-black); }

  .brand {
    position: absolute;
    left: 210px;
    top: 42px;
    width: 250px;
    text-align: center;
  }
  .brand__name {
    font-weight: 400;
    font-size: 24px;
    letter-spacing: 1px;
    color: var(--ink);
    text-transform: uppercase;
    border-bottom: 1px solid var(--ink);
    padding-bottom: 3px;
  }
  .brand__role {
    font-weight: 300;
    font-size: 10px;
    letter-spacing: 3px;
    text-transform: uppercase;
    margin-top: 3px;
  }

  .contact {
    position: absolute;
    left: 34px;
    top: 118px;
  }
  .contact__name {
    font-family: "Sue Ellen Francisco", "Roboto", cursive;
    font-size: 24px;
    letter-spacing: 2px;
    margin-bottom: 4px;
  }
  .contact__web {
    font-size: 20px;
    font-weight: 300;
    letter-spacing: 1px;
    color: var(--accent-red);
    margin-bottom: 10px;
  }
  .contact__list { list-style: none; }
  .contact__item {
    display: flex;
    align-items: center;
    gap: 10px;
    font-size: 14px;
    font-weight: 300;
    letter-spacing: 0.8px;
    margin-bottom: 6px;
  }
  .contact__icon {
    width: 14px;
    height: 14px;
    flex: none;
  }

  .portrait {
    position: absolute;
    right: 24px;
    bottom: 0;
    width: 170px;
    height: 210px;
    background: linear-gradient(180deg, #9a9a9a 0%, #3e3e3e 100%);
    border-radius: 60px 60px 0 0;
  }

  .back-art { position: absolute; inset: 0; }
  .back-web {
    position: absolute;
    right: 28px;
    bottom: 40px;
    font-size: 21px;
    font-weight: 300;
    letter-spacing: 1.5px;
    color: var(--white);
  }
</style>
</head>
<body>

  <section class="card card--front">
    <div class="brand">
      <div class="brand__name">Tobias Lendhart</div>
      <div class="brand__role">Personal Trainer</div>
    </div>

    <div class="contact">
      <p class="contact__name">Tobias Lendhart</p>
      <p class="contact__web">www.tobiaslendhart.de</p>
      <ul class="contact__list">
        <li class="contact__item">
          <svg class="contact__icon" viewBox="0 0 14 14" aria-hidden="true">
            <rect width="14" height="14" fill="#1a1a1a"/>
            <path d="M4 3.5 L5.6 3.5 L6.2 5.4 L5.2 6.1 Q6 7.9 7.9 8.8 L8.6 7.8 L10.5 8.4 L10.5 10 Q6.5 10.5 3.8 6.3 Q3.4 4.8 4 3.5 Z" fill="#fff"/>
          </svg>
          0162/3819204
        </li>
        <li class="contact__item">
          <svg class="contact__icon" viewBox="0 0 14 14" aria-hidden="true">
            <rect width="14" height="14" fill="#1a1a1a"/>
            <rect x="3" y="4" width="8" height="6" fill="none" stroke="#fff" stroke-width="1"/>
            <path d="M3 4 L7 7.5 L11 4" fill="none" stroke="#fff" stroke-width="1"/>
          </svg>
          t.lendhart@mailpost.de
        </li>
        <li class="contact__item">
          <svg class="contact__icon" viewBox="0 0 14 14" aria-hidden="true">
            <rect width="14" height="14" fill="#1a1a1a"/>
            <path d="M7 11.5 Q3.8 7.8 3.8 6 A3.2 3.2 0 0 1 10.2 6 Q10.2 7.8 7 11.5 Z" fill="#fff"/>
            <circle cx="7" cy="6" r="1.2" fill="#1a1a1a"/>
          </svg>
          Wiesengrundweg 14, 80417 München
        </li>
      </ul>
    </div>

    <div class="portrait" role="img" aria-label="Black and white portrait of the trainer standing with arms crossed"></div>
  </section>

  <section class="card card--back">
    <svg class="back-art" viewBox="0 0 540 349" aria-hidden="true">
      <defs>
        <linearGradient id="photoTone" x1="0" y1="0" x2="1" y2="1">
          <stop offset="0" stop-color="#6b5a58"/>
          <stop offset="0.5" stop-color="#8d9496"/>
          <stop offset="1" stop-color="#5d6264"/>
        </linearGradient>
      </defs>
      <ellipse cx="330" cy="-40" rx="300" ry="266" fill="var(--band)"/>
      <ellipse cx="330" cy="-40" rx="292" ry="258" fill="none" stroke="#ffffff" stroke-width="2"/>
      <ellipse cx="330" cy="-40" rx="287" ry="253" fill="url(#photoTone)"/>
    </svg>
    <div role="img" aria-label="Photo of an athlete gripping a loaded barbell for a deadlift" style="position:absolute;left:60px;top:0;width:440px;height:200px;"></div>
    <p class="back-web">www.tobiaslendhart.de</p>
  </section>

</body>
</html>
```